Maple Grove Schools | brand new stationery!

We need stationery design with our new logo! Our company updated it's name and image and we like to incorporate the new one on our stationery, business cards and email signature. We are looking for fresh, new ideas!
Industry: Childcare, Elementary and Middle School
Company Name: Maple Grove Schools
Tagline: Bright Futures Start Here
Main colors: Blue, white and a little yellow
Star shape is something new for us! Do you see a way to incorporate it as a design element?

```html
<!DOCTYPE html>
<html lang="en">
<head>
<meta charset="utf-8">
<title>Maple Grove Schools – Business Card</title>
<link href="https://fonts.googleapis.com/css2?family=Montserrat:wght@500;600&family=Roboto:wght@400&display=swap" rel="stylesheet">
<style>
  :root {
    --backdrop: #2b2b2b;
    --card-dark: #262324;
    --card-light: #ffffff;
    --navy: #0b1f72;
    --gold: #fcc218;
    --silver: #c9c9c9;
    --ink: #555555;
  }
  html, body {
    margin: 0;
    width: 1200px;
    height: 960px;
    overflow: hidden;
    background: var(--backdrop);
  }
  .canvas {
    position: relative;
    width: 1200px;
    height: 960px;
  }
  .card {
    position: absolute;
    left: 320px;
    width: 560px;
    height: 320px;
    border-radius: 22px;
    border-bottom: 4px solid var(--gold);
    box-sizing: border-box;
    overflow: hidden;
  }
  .card--front { top: 110px; background: var(--card-dark); }
  .card--back { top: 520px; background: var(--card-light); }

  .front-brand {
    position: absolute;
    inset: 0;
    display: flex;
    flex-direction: column;
    align-items: center;
    justify-content: center;
    gap: 14px;
  }
  .brand-dot {
    width: 40px; height: 40px;
    border-radius: 50%;
    background: var(--navy);
  }
  .front-name {
    font-family: "Montserrat", sans-serif;
    font-weight: 500;
    font-size: 40px;
    line-height: 1.05;
    color: var(--silver);
    text-align: center;
  }

  .back-brand {
    position: absolute;
    left: 0; bottom: 0;
    width: 300px; height: 240px;
    background: var(--navy);
    border-top-right-radius: 60px;
    display: flex;
    flex-direction: column;
    justify-content: flex-end;
    padding: 0 0 34px 30px;
    box-sizing: border-box;
    gap: 12px;
  }
  .back-brand .brand-dot { background: var(--gold); width: 34px; height: 34px; }
  .back-brand-name {
    font-family: "Montserrat", sans-serif;
    font-weight: 600;
    font-size: 30px;
    line-height: 1.1;
    color: #ffffff;
  }

  .contact {
    position: absolute;
    right: 28px;
    top: 42px;
    text-align: right;
    font-family: "Roboto", sans-serif;
  }
  .contact-name {
    font-family: "Montserrat", sans-serif;
    font-weight: 600;
    font-size: 22px;
    color: var(--navy);
    letter-spacing: 0.5px;
    margin: 0;
  }
  .contact-role {
    font-size: 14px;
    color: var(--gold);
    margin: 0 0 14px;
  }
  .contact-list {
    list-style: none;
    margin: 0; padding: 0;
    font-size: 13px;
    color: var(--ink);
    line-height: 1.45;
  }
  .contact-list li {
    display: flex;
    justify-content: flex-end;
    align-items: flex-start;
    gap: 8px;
  }
  .contact-list svg {
    width: 12px; height: 12px;
    margin-top: 3px;
    fill: var(--navy);
    flex: none;
  }
  .icon-spacer { width: 12px; flex: none; }
</style>
</head>
<body>
<main class="canvas">
  <section class="card card--front" aria-label="Card front">
    <div class="front-brand">
      <span class="brand-dot"></span>
      <div class="front-name">Maple Grove<br>Schools</div>
    </div>
  </section>

  <section class="card card--back" aria-label="Card back">
    <div class="back-brand">
      <span class="brand-dot"></span>
      <div class="back-brand-name">Maple Grove<br>Schools</div>
    </div>

    <div class="contact">
      <p class="contact-name">DANIEL CARTER</p>
      <p class="contact-role">President</p>
      <ul class="contact-list">
        <li><span>412 Willow Bend Road<br>Fairbanks, Alaska 99701</span>
          <svg viewBox="0 0 12 12"><path d="M6 0a4 4 0 0 0-4 4c0 3 4 8 4 8s4-5 4-8a4 4 0 0 0-4-4zm0 5.5A1.5 1.5 0 1 1 6 2.5a1.5 1.5 0 0 1 0 3z"/></svg></li>
        <li><span>555-214-7730</span>
          <svg viewBox="0 0 12 12"><path d="M2 0l2 2.5-1 1.5c.8 1.8 2.2 3.2 4 4l1.5-1L11 9l-1.5 2.5C5 11 1 7 .5 2.5z"/></svg></li>
        <li><span>555-318-4462</span>
          <svg viewBox="0 0 12 12"><path d="M3 0h6a1 1 0 0 1 1 1v10a1 1 0 0 1-1 1H3a1 1 0 0 1-1-1V1a1 1 0 0 1 1-1zm0 1.5v8h6v-8z"/></svg></li>
        <li><span>555-402-9185</span>
          <svg viewBox="0 0 12 12"><path d="M3 0h6v3H3zM0 4h12v6h-2v2H2v-2H0zm3 4v3h6V8z"/></svg></li>
        <li><span>info@maplegroveschools.com</span>
          <svg viewBox="0 0 12 12"><path d="M0 2h12v8H0zm1 1v.5l5 3 5-3V3z"/></svg></li>
        <li><span>maplegroveschools.com</span>
          <svg viewBox="0 0 12 12"><circle cx="6" cy="6" r="6"/></svg></li>
      </ul>
    </div>
  </section>
</main>
</body>
</html>
```